Corvane Freight Company Business Card Design

We are a company that delivers natural saltwater (from the ocean) to aquarium companies, restaurants and home marine tanks. I would like a new business card to suit.

Must include Name, company name, abn, contact number and website as well as logo (see attached).

Looking for a design that stands out, has a clean but unique appearance.

Double and single sided entries welcome

Business

• Logo

```html
<!DOCTYPE html>
<html lang="en">
<head>
<meta charset="utf-8">
<title>Corvane Freight Company – Business Card</title>
<link rel="stylesheet" href="https://fonts.googleapis.com/css2?family=Jost:wght@400;600&display=swap">
<style>
  :root {
    --backdrop: #2a2a2c;
    --card-blue: #1766f2;
    --accent-aqua: #bfeeff;
    --ink-white: #ffffff;
    --ink-soft: #e6efff;
  }
  * { box-sizing: border-box; margin: 0; padding: 0; }
  html, body {
    width: 1200px; height: 1086px; overflow: hidden;
    background: var(--backdrop);
    font-family: "Jost", "Futura", sans-serif;
  }
  .canvas { position: relative; width: 1200px; height: 1086px; }

  .card {
    position: absolute;
    width: 778px; height: 444px;
    background: var(--card-blue);
    border-radius: 34px;
    color: var(--ink-white);
  }
  .card--front { left: 67px; top: 67px; }
  .card--back  { left: 342px; top: 564px; }

  .accent-bar { position: absolute; width: 6px; background: var(--accent-aqua); }
  .accent-bar--left  { left: 2px; top: 44px; height: 126px; }
  .accent-bar--right { left: 770px; top: 182px; height: 213px; }

  .brand {
    position: absolute;
    display: flex; align-items: center; gap: 14px;
    font-weight: 600; color: var(--ink-white); white-space: nowrap;
  }
  .brand__dot { border-radius: 50%; background: var(--accent-aqua); flex: none; }
  .card--front .brand { left: 44px; top: 84px; font-size: 44px; }
  .card--front .brand__dot { width: 26px; height: 26px; }
  .card--back .brand { left: 0; right: 0; justify-content: center; top: 160px; font-size: 66px; }
  .card--back .brand__dot { width: 38px; height: 38px; }

  .details {
    position: absolute; right: 28px; top: 152px;
    text-align: right; color: var(--ink-soft);
  }
  .details__name { font-size: 27px; font-weight: 600; color: var(--ink-white); margin-bottom: 18px; }
  .details__title { font-weight: 400; font-size: 21px; }
  .details__line { font-size: 20px; line-height: 29px; display: flex; justify-content: flex-end; align-items: center; gap: 6px; }
  .details__line svg { width: 15px; height: 15px; }
  .details__company { font-size: 21px; margin-top: 17px; line-height: 28px; }
  .details__address { font-size: 19px; line-height: 26px; }

  .back-web {
    position: absolute; left: 0; right: 0; top: 360px;
    text-align: center; font-size: 25px; letter-spacing: 0.2em;
    color: var(--ink-soft);
  }
</style>
</head>
<body>
<main class="canvas">
  <section class="card card--front">
    <span class="accent-bar accent-bar--left"></span>
    <span class="accent-bar accent-bar--right"></span>
    <div class="brand"><span class="brand__dot"></span>Corvane Freight</div>
    <div class="details">
      <p class="details__name">Your name, <span class="details__title">Title</span></p>
      <p class="details__line">
        <svg viewBox="0 0 16 16" aria-hidden="true"><circle cx="8" cy="8" r="7" fill="none" stroke="currentColor" stroke-width="1.4"/><path d="M5.5 4.5c0 3.5 2.5 6.5 5.5 7l1-1.5-1.8-1-1 .8c-1-.5-2-1.5-2.4-2.5l.8-1-1-1.8z" fill="currentColor"/></svg>
        123-456-7890
      </p>
      <p class="details__line">
        <svg viewBox="0 0 16 16" aria-hidden="true"><circle cx="8" cy="8" r="7" fill="currentColor"/><path d="M1 8h14M8 1c-3 3-3 11 0 14M8 1c3 3 3 11 0 14" stroke="#1766f2" stroke-width="1" fill="none"/></svg>
        www.website.com
      </p>
      <p class="details__line">ABN : 0123456789</p>
      <p class="details__company">Corvane Freight Company</p>
      <p class="details__address">Street Name, City Name, State, City Zip Code</p>
    </div>
  </section>

  <section class="card card--back">
    <div class="brand"><span class="brand__dot"></span>Corvane Freight</div>
    <p class="back-web">www.website.com</p>
  </section>
</main>
</body>
</html>
```